Luxury Wine Label for New Startup Winery

We need a wine label for our new winery startup. We have worked with a local designer but do not feel the resulting label / logo have the elevation required to present our brand as a luxury wine. Our winery is called "Quailbrook Vineyards" and we are focused on extremely high quality hand crafted artisan and estate wines from the Pacific Northwest.
We would like to see designs that utilize a tree line, or other imagery that represents the "Quailbrook" part of our company name. Another interesting feature could be wood grain.
A logo will be required based on your design so please design with this in mind:
This logo should be consistent with the wine bottle label design, and should be representative of our high end exclusive wine while giving a sense of place (Oregon/ Pacific Northwest.)
I will supply an image of the design we received from our local designer, PLEASE NOTE: in general we do like wood grain and tree line concepts but feel the execution was poorly done.
ATTN: Logo design should be suitable for use on: Bottles (Red wine/rose/white wine), Bussiness cards, vehicle signage, business signage, etc
P.S.:
If you have a design that is not outside the box we are still interested in seeing it.
Label is for a burgundy style bottle with a label height of 3.5 - 4" and a width of 3.5-4"
any label <= 4"x4" and >=3.5"x3.5" will be acceptable:
HOWEVER Width should be greater than or equal to height due to the bottle format
Target Market(s)
Wine enthusiasts with adequate discretionary budgets to afford $100 bottles of wine.
Industry/Entity Type
Wine / Winery
Requirements
Must have
- A sense of luxury, a feel of exclusivity, and a theme consistent with our product and brand name
Nice to have
- Tree line, wood grain or other wood themes. Serif fonts
Should not have
- anything cheesy, off topic, hard to read script fonts or anything that makes the label hard to read from a few feet away or too busy

```html
<!DOCTYPE html>
<html lang="en">
<head>
<meta charset="utf-8">
<title>Quailbrook Vineyards – Wine Labels</title>
<link rel="stylesheet" href="https://fonts.googleapis.com/css2?family=Cormorant+Garamond:wght@500;600;700&display=swap">
<style>
  :root {
    --backdrop: #2a2a2c;
    --rose-paper: #f2efee;
    --rose-ink: #9c1f2e;
    --rose-tree-a: #b8283c;
    --rose-tree-b: #d9728a;
    --rose-hill: #efd9dc;
    --rose-rule: #a9a9a9;
    --syrah-paper: #1d1d1f;
    --syrah-ink: #c9a44a;
    --syrah-tree-a: #b88f35;
    --syrah-tree-b: #e2c774;
    --syrah-hill: #2a2a2c;
    --wood-dark: #4a2a1e;
    --wood-mid: #7a4a36;
    --wood-light: #9a6650;
    --wood-deep: #2a1a12;
    --wood-deep-mid: #4a3020;
    --band-ink-light: #ece6e2;
  }
  * { box-sizing: border-box; margin: 0; padding: 0; }
  html, body { width: 1200px; height: 900px; overflow: hidden; }
  body {
    background: var(--backdrop);
    font-family: "Cormorant Garamond", Georgia, serif;
    position: relative;
  }
  .label-set { position: absolute; top: 120px; width: 470px; }
  .label-set--rose { left: 85px; }
  .label-set--syrah { left: 645px; }

  .main-label {
    position: relative;
    height: 380px;
    border-radius: 14px;
    overflow: hidden;
    text-align: center;
  }
  .label-set--rose .main-label { background: var(--rose-paper); color: var(--rose-ink); }
  .label-set--syrah .main-label { background: var(--syrah-paper); color: var(--syrah-ink); }

  .main-label__art { position: absolute; inset: 0; width: 100%; height: 100%; }

  .tree-line {
    position: absolute;
    left: 40px; right: 40px; top: 78px;
    height: 70px;
    clip-path: polygon(0 100%, 0 70%, 30% 40%, 55% 10%, 100% 0, 100% 40%, 60% 55%, 30% 80%, 8% 100%);
  }
  .label-set--rose .tree-line { background: linear-gradient(90deg, var(--rose-tree-a), var(--rose-tree-b) 55%, var(--rose-tree-a)); }
  .label-set--syrah .tree-line { background: linear-gradient(90deg, var(--syrah-tree-a), var(--syrah-tree-b) 45%, var(--syrah-tree-a)); }

  .brand-name {
    position: absolute; left: 0; right: 0; top: 162px;
    font-size: 68px; font-weight: 600; line-height: 1;
    letter-spacing: 0.5px;
  }
  .brand-sub {
    position: absolute; left: 0; right: 0; top: 236px;
    display: flex; align-items: center; justify-content: center; gap: 16px;
    font-size: 17px; font-weight: 600; letter-spacing: 9px;
  }
  .brand-sub::before, .brand-sub::after {
    content: ""; width: 70px; height: 1.5px; background: currentColor;
  }
  .region {
    position: absolute; left: 0; right: 0; top: 282px;
    font-size: 13px; font-weight: 600; letter-spacing: 5px;
  }
  .label-set--rose .region { color: #6d6d6d; }

  .varietal-band {
    position: relative;
    margin-top: 40px;
    height: 170px;
    border-radius: 12px;
    overflow: hidden;
    text-align: center;
  }
  .varietal-band__wood { position: absolute; inset: 0; }
  .label-set--rose .varietal-band__wood {
    background: linear-gradient(100deg, var(--wood-dark), var(--wood-mid) 35%, var(--wood-light) 55%, var(--wood-mid) 80%, var(--wood-dark));
  }
  .label-set--syrah .varietal-band__wood {
    background: linear-gradient(100deg, var(--wood-deep), var(--wood-deep-mid) 45%, var(--wood-deep) 90%);
  }
  .varietal-band__rules { position: absolute; inset: 0; width: 100%; height: 100%; }
  .varietal {
    position: relative;
    padding-top: 48px;
    font-size: 50px; font-weight: 600; letter-spacing: 14px; line-height: 1;
  }
  .vintage {
    position: relative;
    margin-top: 18px;
    font-size: 15px; font-weight: 600; letter-spacing: 2px;
  }
  .label-set--rose .varietal-band { color: var(--band-ink-light); }
  .label-set--syrah .varietal-band { color: var(--syrah-ink); }
</style>
</head>
<body>

<section class="label-set label-set--rose" aria-label="Rosé label">
  <div class="main-label">
    <svg class="main-label__art" viewBox="0 0 470 380" preserveAspectRatio="none" aria-hidden="true">
      <path d="M0 240 L90 200 L170 225 L260 170 L360 215 L470 190 L470 380 L0 380 Z" fill="var(--rose-hill)"/>
      <path d="M30 60 Q235 20 440 50" fill="none" stroke="var(--rose-rule)" stroke-width="1.5"/>
      <path d="M25 330 Q120 310 230 325 Q340 340 445 318" fill="none" stroke="var(--rose-rule)" stroke-width="1.5"/>
    </svg>
    <div class="tree-line" role="img" aria-label="Silhouetted evergreen tree line rising across the label"></div>
    <div class="brand-name">Quailbrook</div>
    <div class="brand-sub">VINEYARDS</div>
    <div class="region">WILLAMETTE VALLEY</div>
  </div>
  <div class="varietal-band">
    <div class="varietal-band__wood" role="img" aria-label="Warm wood grain texture"></div>
    <svg class="varietal-band__rules" viewBox="0 0 470 170" preserveAspectRatio="none" aria-hidden="true">
      <path d="M20 28 Q235 10 450 28" fill="none" stroke="var(--band-ink-light)" stroke-width="1.5" opacity="0.8"/>
      <path d="M20 140 L110 130 M360 130 L450 140" fill="none" stroke="var(--band-ink-light)" stroke-width="1.5" opacity="0.8"/>
    </svg>
    <div class="varietal">ROSÉ</div>
    <div class="vintage">ESTATE | 2023 | GROWN</div>
  </div>
</section>

<section class="label-set label-set--syrah" aria-label="Syrah label">
  <div class="main-label">
    <svg class="main-label__art" viewBox="0 0 470 380" preserveAspectRatio="none" aria-hidden="true">
      <path d="M0 240 L90 200 L170 225 L260 170 L360 215 L470 190 L470 380 L0 380 Z" fill="var(--syrah-hill)"/>
      <path d="M30 60 Q235 20 440 50" fill="none" stroke="#6a6a6a" stroke-width="1.5"/>
      <path d="M25 330 Q120 310 230 325 Q340 340 445 318" fill="none" stroke="#6a6a6a" stroke-width="1.5"/>
    </svg>
    <div class="tree-line" role="img" aria-label="Gold evergreen tree line rising across the label"></div>
    <div class="brand-name">Quailbrook</div>
    <div class="brand-sub">VINEYARDS</div>
    <div class="region">WILLAMETTE VALLEY</div>
  </div>
  <div class="varietal-band">
    <div class="varietal-band__wood" role="img" aria-label="Dark wood grain texture"></div>
    <svg class="varietal-band__rules" viewBox="0 0 470 170" preserveAspectRatio="none" aria-hidden="true">
      <path d="M20 28 Q235 10 450 28" fill="none" stroke="var(--syrah-ink)" stroke-width="1.5"/>
      <path d="M20 140 L110 130 M360 130 L450 140" fill="none" stroke="var(--syrah-ink)" stroke-width="1.5"/>
    </svg>
    <div class="varietal">SYRAH</div>
    <div class="vintage">ESTATE | 2023 | GROWN</div>
  </div>
</section>

</body>
</html>
```